Fitness Equipment Repair Business Needs a Catchy New Business Card

We have an existing business card, however, it is quite plain and boring. We are expanding primarily in the commercial area (gyms, studios, apartment complexes etc). The business card will serve as eye candy to those managers/owners that can't be met for a face to face.
Originally I was planning for a brochure as well, but all of our information is better summarized on our website. (brightloopservice.ca).
I would like the card to match the colour scheme of the website and utilize the logo. It should have a professional clean feel to it, however, a little colouring outside the lines wouldn't hurt.
The example card is for my service technician (Colin Marsh). If possible I would like to be able to edit the text to use for more than one person.

Industry/Entity Type

Appliance Repair

Contact Information for Business Card

Clean, crisp and professional but needs to be eye catching. Preferably using the black, white and red colour scheme matching the website. Double sided would be nice, but is not necessary.

Colors
ec1f27
ffffff
000000

Requirements
Must have
• Must be able to edit name, phone number and title to use for multiple people. Must show the company website (brightloopservice.ca).

```html
<!DOCTYPE html>
<html lang="en">
<head>
<meta charset="utf-8">
<title>Bright Loop Service – Business Card</title>
<link rel="stylesheet" href="https://fonts.googleapis.com/css2?family=Open+Sans:wght@400;700&family=Tinos:wght@700&family=Tenor+Sans&display=swap">
<style>
  :root {
    --bg: #ececec;
    --card-white: #ffffff;
    --card-black: #0b0b0b;
    --ink: #111111;
    --ink-soft: #333333;
    --red: #ec1f27;
    --white: #ffffff;
  }
  * { box-sizing: border-box; margin: 0; padding: 0; }
  html, body { width: 1200px; height: 900px; overflow: hidden; }
  body {
    background: var(--bg);
    position: relative;
    font-family: "Open Sans", sans-serif;
  }
  .card {
    position: absolute;
    top: 307px;
    width: 500px;
    height: 286px;
    box-shadow: 0 6px 18px rgba(0,0,0,0.12);
  }
  .card-front { left: 70px; background: var(--card-white); color: var(--ink); }
  .card-back { left: 630px; background: var(--card-black); color: var(--white); }

  .person { position: absolute; left: 34px; top: 30px; }
  .person-name { font-weight: 700; font-size: 17px; line-height: 1.2; }
  .person-title { font-size: 12px; color: var(--ink-soft); margin-top: 2px; }

  .contact { position: absolute; left: 34px; top: 86px; list-style: none; font-size: 12px; line-height: 1.5; color: var(--ink-soft); }
  .contact li { display: flex; align-items: flex-start; gap: 7px; }
  .contact .address { padding-left: 17px; margin-bottom: 2px; }
  .contact svg { width: 10px; height: 10px; margin-top: 4px; flex: none; fill: var(--ink); }

  .tagline {
    position: absolute; left: 34px; top: 196px; width: 300px;
    font-family: "Tinos", serif; font-weight: 700; font-size: 13px;
    text-transform: uppercase; line-height: 1.3; color: var(--ink);
  }

  .brand-mark { position: absolute; display: flex; align-items: center; gap: 8px; }
  .card-front .brand-mark { right: 30px; top: 128px; }
  .brand-mark .dot { width: 12px; height: 12px; border-radius: 50%; background: var(--red); flex: none; }
  .brand-mark .brand-name { font-family: "Open Sans", sans-serif; font-weight: 700; font-size: 15px; color: var(--red); text-transform: uppercase; letter-spacing: 0.5px; }
  .card-back .brand-mark { left: 40px; top: 134px; }

  .company-title {
    position: absolute; left: 238px; top: 82px;
    font-family: "Tenor Sans", sans-serif; font-size: 34px;
    font-variant: small-caps; letter-spacing: 2px; line-height: 1.05;
    color: var(--white);
  }
</style>
</head>
<body>
  <section class="card card-front">
    <div class="person">
      <div class="person-name">Colin Marsh</div>
      <div class="person-title">Managing Director</div>
    </div>
    <ul class="contact">
      <li class="address">1234, Address GoesHere,<br>Country, 12345</li>
      <li><svg viewBox="0 0 10 10"><path d="M2 0h2l1 2.5-1.3 1a5 5 0 0 0 2.8 2.8l1-1.3L10 6v2a2 2 0 0 1-2 2A8 8 0 0 1 0 2a2 2 0 0 1 2-2z"/></svg>(044) 123456789</li>
      <li><svg viewBox="0 0 10 10"><rect x="0" y="2" width="10" height="7" rx="1"/></svg>(044)123456789</li>
      <li><svg viewBox="0 0 10 10"><path d="M0 2h10v7H0z M0 2l5 4 5-4" stroke="#fff" stroke-width="0.8"/></svg>info@brightloopmail.com</li>
      <li><svg viewBox="0 0 10 10"><circle cx="5" cy="5" r="5"/></svg>www.brightloopservice.ca</li>
    </ul>
    <p class="tagline">When your equipment can't finish their workout,<br>give us a call!</p>
    <div class="brand-mark">
      <span class="dot"></span>
      <span class="brand-name">Bright Loop Service</span>
    </div>
  </section>

  <section class="card card-back">
    <div class="brand-mark">
      <span class="dot"></span>
      <span class="brand-name">Bright Loop</span>
    </div>
    <h1 class="company-title">Bright<br>Loop<br>Service</h1>
  </section>
</body>
</html>
```